Financial Services General Marketing Brochure

Need a brochure to help recipients understand what makes BWC unique and the services that we offer. Must match look/feel of website https://brightwellcustody.example Layouts should make it easy to read the content - content should not be crammed into a traditional size/layout. Please see attached creative brief for specifics.

Target Market(s)

Financial advisors and mature couples looking for trustee services.

Industry/Entity Type

Financial Service

Colors
34a7d8
ffc214

Requirements
Must have
• See Creative Brief

```html
<!DOCTYPE html>
<html lang="en">
<head>
<meta charset="utf-8">
<title>BWC Brochure Spread</title>
<link href="https://fonts.googleapis.com/css2?family=Open+Sans:wght@400;600;700&family=Source+Serif+4:ital,opsz,wght@0,8..60,400;1,8..60,400&display=swap" rel="stylesheet">
<style>
:root{
  --page:#ffffff;
  --cream:#fdfbf6;
  --beige:#f6efe5;
  --slate:#54728f;
  --slate-dark:#4a6987;
  --navy-text:#3d5570;
  --gold:#e9ad3a;
  --body:#5a5a5a;
  --ring:#d9c6ad;
  --rule:#d8d8d8;
}
*{margin:0;padding:0;box-sizing:border-box}
html,body{width:1200px;height:641px;overflow:hidden;background:var(--page)}
body{position:relative;font-family:"Open Sans",Arial,sans-serif}
h2,h3{font-weight:400}
.rule{position:absolute;left:0;width:1200px;height:1px;background:var(--rule)}
.rule.top{top:20px}.rule.bottom{top:620px}
.edge{position:absolute;top:20px;width:1px;height:601px;background:var(--rule)}
.fold{position:absolute;left:600px;top:0;height:641px;border-left:1px dashed #cfcfcf}

/* left panel */
.intro-photo{position:absolute;left:0;top:21px;width:300px;height:166px;
  background:linear-gradient(120deg,#6f5a45 0%,#a08a70 30%,#2e3f5c 55%,#8a95a3 80%,#c9c3b8 100%)}
.intro{position:absolute;left:0;top:187px;width:300px;height:433px;background:var(--slate);color:#fff;padding:38px 38px 0 42px}
.intro p{font-family:"Source Serif 4",Georgia,serif;font-size:11.2px;line-height:17.5px;margin-bottom:17px}
.dropcap{float:left;font-size:58px;line-height:46px;margin:3px 5px 0 0}
.signature{position:absolute;left:94px;top:368px;font-size:12.5px;line-height:18px}
.signature strong{font-weight:600;display:block}

/* middle panel */
.unique-head{position:absolute;left:300px;top:55px;width:300px;height:65px;background:var(--beige);
  display:flex;align-items:center;padding-left:18px;
  font-family:"Source Serif 4",Georgia,serif;font-size:21px;color:var(--slate)}
.traits{position:absolute;left:326px;top:153px;width:252px}
.trait{margin-bottom:13px}
.trait h3{font-family:"Source Serif 4",Georgia,serif;font-style:italic;font-size:15px;color:var(--gold);margin-bottom:3px}
.trait p{font-size:10.5px;line-height:14.7px;color:var(--body)}

/* right panel */
.team{position:absolute;left:601px;top:21px;width:599px;height:599px;background:var(--cream)}
.team-head{position:absolute;left:601px;top:55px;width:599px;height:65px;background:var(--slate-dark);
  color:#fff;text-align:center;font-family:"Source Serif 4",Georgia,serif;font-size:20px;line-height:25px;padding-top:8px}
.team-map{position:absolute;left:601px;top:120px}
.node-label{font-family:"Open Sans",Arial,sans-serif;font-weight:700;fill:var(--navy-text)}
.small-label{font-family:"Open Sans",Arial,sans-serif;font-weight:700;fill:#fff;font-size:7.5px}
.tiny{font-family:"Source Serif 4",Georgia,serif;fill:var(--navy-text);font-size:5.6px}
</style>
</head>
<body>
<div class="rule top"></div><div class="rule bottom"></div>
<div class="edge" style="left:0"></div><div class="edge" style="left:1199px"></div>

<section class="panel-intro">
  <div class="intro-photo" role="img" aria-label="Photo of a smiling advisor in a navy blazer meeting with a client"></div>
  <div class="intro">
    <p><span class="dropcap">W</span>e understand that wealth and families is very complex. As families try to transfer wealth it can be an incredible blessing or, if done improperly, can be incredibly destructive. Often a neutral third party is needed to come alongside the family's advisory team to provide guidance as families go through their wealth transition.</p>
    <p>Our relational focus, and Open Framework approach, helps families to successfully navigate through the complexities of wealth, family and trusts. We believe a family "legacy" is about more than just money.</p>
    <div class="signature"><strong>Daniel Harlow, J.D.</strong>Founding Principal</div>
  </div>
</section>

<section class="panel-unique">
  <h2 class="unique-head">What Makes BWC Unique</h2>
  <div class="traits">
    <div class="trait"><h3>Responsive</h3><p>The family deals directly with decision makers instead of being subject to committees with whom the family may never have the opportunity to interact or engage.</p></div>
    <div class="trait"><h3>Family Focus</h3><p>We help families successfully navigate the complexities of family wealth, not just perform trust administration.</p></div>
    <div class="trait"><h3>Independent</h3><p>To avoid any conflicts of interest, we have no formal affiliations with wealth management firms or financial advisory practices.</p></div>
    <div class="trait"><h3>Customized</h3><p>Together we develop a customized approach that will best suit the family's needs.</p></div>
    <div class="trait"><h3>Collaborative</h3><p>We work collaboratively with the family's team of trusted professionals.</p></div>
  </div>
</section>

<div class="fold"></div>

<section class="panel-team">
  <div class="team"></div>
  <h2 class="team-head">Brightwell Custody Group<br>Client/Family Centered Team</h2>
  <svg class="team-map" width="599" height="500" viewBox="0 0 599 500">
    <defs>
      <linearGradient id="warm" x1="0" y1="0" x2="1" y2="1"><stop offset="0" stop-color="#7d8a5a"/><stop offset=".5" stop-color="#c79a7a"/><stop offset="1" stop-color="#5b4636"/></linearGradient>
      <linearGradient id="soft" x1="0" y1="0" x2="1" y2="1"><stop offset="0" stop-color="#f1e4da"/><stop offset="1" stop-color="#c7b7ab"/></linearGradient>
      <linearGradient id="couple" x1="0" y1="0" x2="1" y2="1"><stop offset="0" stop-color="#8e9a6a"/><stop offset=".5" stop-color="#d7b49c"/><stop offset="1" stop-color="#b9b2a8"/></linearGradient>
    </defs>
    <g stroke="var(--ring)" stroke-width="3">
      <line x1="188" y1="210" x2="205" y2="210"/><line x1="400" y1="210" x2="416" y2="210"/>
      <line x1="240" y1="290" x2="228" y2="298"/><line x1="365" y1="290" x2="380" y2="298"/>
    </g>
    <g role="img" aria-label="Photo of a smiling woman, the current beneficiary">
      <circle cx="229" cy="80" r="62" fill="url(#warm)" stroke="var(--ring)" stroke-width="3"/>
      <text class="small-label" x="229" y="123" text-anchor="middle">Current Beneficiary</text>
    </g>
    <g role="img" aria-label="Photo of two young children, the future beneficiaries">
      <circle cx="375" cy="80" r="58" fill="url(#soft)" stroke="var(--ring)" stroke-width="3"/>
      <text class="small-label" x="375" y="123" text-anchor="middle">Future Beneficiary</text>
    </g>
    <g role="img" aria-label="Photo of a smiling older couple, the trust creators">
      <polygon points="240,132 365,132 403,212 365,292 240,292 202,212" fill="url(#couple)" stroke="var(--ring)" stroke-width="3"/>
      <text class="node-label" x="303" y="285" text-anchor="middle" font-size="12">Trust Creator</text>
    </g>
    <g fill="#fff" stroke="var(--ring)" stroke-width="3">
      <circle cx="130" cy="210" r="59"/><circle cx="474" cy="210" r="59"/>
      <circle cx="205" cy="340" r="57"/><circle cx="404" cy="344" r="57"/>
      <circle cx="307" cy="425" r="58"/>
    </g>
    <text class="node-label" x="130" y="215" text-anchor="middle" font-size="13">Attorney</text>
    <text class="node-label" x="474" y="215" text-anchor="middle" font-size="13">Accountant</text>
    <text class="node-label" x="205" y="345" text-anchor="middle" font-size="13">Financial</text>
    <text class="node-label" x="404" y="349" text-anchor="middle" font-size="13">Trustee</text>
    <text class="node-label" x="307" y="410" text-anchor="middle" font-size="11.5">Human Capital</text>
    <text class="node-label" x="307" y="424" text-anchor="middle" font-size="11.5">Resources</text>
    <text class="tiny" x="307" y="437" text-anchor="middle">Legacy Development</text>
    <text class="tiny" x="307" y="446" text-anchor="middle">Health Care Management</text>
    <text class="tiny" x="307" y="455" text-anchor="middle">Philanthropic Services</text>
    <text class="tiny" x="307" y="464" text-anchor="middle">Life Coaching</text>
  </svg>
</section>
</body>
</html>
```